Bref créative
Safety products company
Safety products for life
Professional
Dorian K Pell
President/Founder
482 Quillmere Lane
Hollin Brook, PA 16328-4471
555.01R.GUMA (555.0148)
pell@vornatek.com
www.vornatek.com
BE PREPARED
HOME
DISASTER
CHILD
SENIOR
PET
TRAVEL
LIVE SAFELY
the logo
"stacked" logo - two more will be coming with white backgrounds as soon as I receive them
4 AI LOGOS

```html
<!DOCTYPE html>
<html lang="en">
<head>
<meta charset="utf-8">
<title>Vornatek Stationery Set</title>
<link href="https://fonts.googleapis.com/css2?family=Open+Sans:wght@400;700&display=swap" rel="stylesheet">
<style>
:root{
  --board:#3b3b3c;
  --paper:#ffffff;
  --red:#b3241c;
  --red-deep:#7e140f;
  --ink:#555555;
  --ink-soft:#9a9a9a;
  --ghost:#f3e6e6;
  --dark:#2a2a2a;
  --label:#bdbdbd;
}
*{margin:0;padding:0;box-sizing:border-box}
html,body{width:1200px;height:317px;overflow:hidden;background:var(--board);font-family:"Open Sans",Arial,sans-serif}
.board{position:relative;width:1200px;height:317px}
.item{position:absolute;background:var(--paper);overflow:hidden;box-shadow:0 1px 3px rgba(0,0,0,.5)}
.label{position:absolute;font-size:4px;color:var(--label);white-space:nowrap}
.brand{display:flex;align-items:center;gap:2px;font-weight:700;color:var(--red);letter-spacing:.3px;white-space:nowrap}
.brand .mark{background:var(--red)}
.corner{position:absolute;width:0;height:0}
.corner.tl{top:0;left:0;border-top:22px solid var(--red);border-right:22px solid transparent}
.corner.br{bottom:0;right:0;border-bottom:22px solid var(--red);border-left:22px solid transparent}
.ghost-square{position:absolute;background:var(--ghost);border-radius:6px}
.fine{font-size:3px;color:var(--ink-soft);line-height:4px;white-space:nowrap}
.card{width:62px;height:38px}
.card .brand{font-size:5px;position:absolute}
.card .brand .mark{width:4px;height:4px}
.card-dark{background:var(--dark)}
.letterhead{width:212px;height:282px;top:16px}
.letterhead .brand{position:absolute;top:12px;left:30px;font-size:9px}
.letterhead .brand .mark{width:7px;height:7px}
.letterhead .footer{position:absolute;bottom:8px;left:0;right:0;text-align:center}
.envelope .brand{position:absolute;font-size:6px}
.envelope .brand .mark{width:5px;height:5px}
.flap{position:absolute;top:0;left:0;width:100%;height:100%}
</style>
</head>
<body>
<main class="board">

  <section class="item card" style="left:20px;top:72px">
    <div class="brand" style="left:14px;top:14px"><span class="mark"></span>VORNATEK</div>
  </section>
  <div class="label" style="left:20px;top:113px">Card Front</div>
  <section class="item card" style="left:88px;top:72px">
    <div style="position:absolute;left:5px;top:6px">
      <p class="fine" style="color:var(--ink);font-weight:700">Dorian K Pell</p>
      <p class="fine">President/Founder</p>
    </div>
    <div style="position:absolute;left:5px;bottom:4px">
      <p class="fine">555.01R.GUMA (555.0148)</p>
      <p class="fine">pell@vornatek.com</p>
    </div>
  </section>
  <div class="label" style="left:88px;top:113px">Card Back</div>
  <section class="item card" style="left:20px;top:125px">
    <span class="corner tl" style="border-top-width:12px;border-right-width:12px"></span>
    <div class="brand" style="left:14px;top:15px"><span class="mark"></span>VORNATEK</div>
  </section>
  <div class="label" style="left:20px;top:166px">Card Front</div>
  <section class="item card card-dark" style="left:88px;top:125px">
    <span style="position:absolute;left:26px;top:14px;width:10px;height:10px;background:var(--red)"></span>
  </section>
  <div class="label" style="left:88px;top:166px">Card Back</div>

  <section class="item letterhead" style="left:185px">
    <span class="corner tl"></span><span class="corner br"></span>
    <div class="brand"><span class="mark"></span>VORNATEK</div>
    <div style="position:absolute;top:40px;left:30px">
      <p class="fine">482 Quillmere Lane</p>
      <p class="fine">Hollin Brook, PA 16328-4471</p>
    </div>
    <div class="ghost-square" style="left:100px;top:175px;width:70px;height:70px"></div>
    <div class="footer"><p class="fine">555.01R.GUMA (555.0148) · pell@vornatek.com · www.vornatek.com</p></div>
  </section>
  <div class="label" style="left:185px;top:302px">Letterhead One</div>

  <section class="item letterhead" style="left:430px">
    <span class="corner tl"></span><span class="corner br"></span>
    <div class="brand" style="left:80px"><span class="mark"></span>VORNATEK</div>
    <div class="ghost-square" style="left:72px;top:120px;width:70px;height:70px"></div>
    <div class="footer"><p class="fine">www.vornatek.com</p></div>
  </section>
  <div class="label" style="left:430px;top:302px">Letterhead Two</div>

  <section class="item envelope" style="left:715px;top:95px;width:200px;height:82px">
    <span class="corner tl"></span>
    <div class="brand" style="left:28px;top:12px"><span class="mark"></span>VORNATEK</div>
    <div style="position:absolute;left:28px;top:22px">
      <p class="fine">482 Quillmere Lane</p>
      <p class="fine">Hollin Brook, PA 16328-4471</p>
    </div>
  </section>
  <div class="label" style="left:715px;top:180px">Envelope Front</div>
  <section class="item envelope" style="left:715px;top:192px;width:200px;height:82px">
    <span class="corner br"></span>
    <svg class="flap" viewBox="0 0 200 82" preserveAspectRatio="none" aria-hidden="true">
      <polyline points="0,0 100,38 200,0" fill="none" stroke="#d8d8d8" stroke-width="1"/>
    </svg>
  </section>
  <div class="label" style="left:715px;top:277px">Envelope Back</div>

  <section class="item" style="left:945px;top:12px;width:235px;height:66px;background:linear-gradient(180deg,var(--red) 0%,var(--red-deep) 100%)">
    <svg class="flap" viewBox="0 0 235 66" preserveAspectRatio="none" aria-hidden="true">
      <polygon points="0,0 117,50 235,0" fill="rgba(0,0,0,.25)"/>
    </svg>
  </section>
  <section class="item" style="left:945px;top:90px;width:235px;height:62px;background:var(--dark)">
    <svg class="flap" viewBox="0 0 235 62" preserveAspectRatio="none" aria-hidden="true">
      <polyline points="0,0 117,38 235,0" fill="none" stroke="#444" stroke-width="1"/>
    </svg>
  </section>
  <section class="item" style="left:945px;top:164px;width:235px;height:62px">
    <span style="position:absolute;left:112px;top:24px;width:12px;height:12px;background:var(--red)"></span>
  </section>
  <section class="item envelope" style="left:945px;top:236px;width:235px;height:62px">
    <span class="corner tl" style="border-top-width:16px;border-right-width:16px"></span>
    <div class="brand" style="left:22px;top:10px"><span class="mark"></span>VORNATEK</div>
  </section>
  <div class="label" style="left:945px;top:302px">Large Envelope</div>

</main>
</body>
</html>
```